Laser Tattoo Removal Business Cards

We are looking for a professional business card design for a laser tattoo removal business. Ideally looking for a black business card design. The name of the business is Brightline Tattoo Removal. We place our cards at local tattoo shops so we ideally are looking for something trendy/edgy to draw both male and female clientele in.

Target Market(s)

Male/Female ages 18-60

Contact Information for Business Card

black background ideally.. hoping to stay within greys, whites and black

Font styles to use
Serif
Sans Serif

Colors
121212
a9a9a9
5c5c5c
f5f5f5
ffffff
7f7f7f
606060
848484
9d9d9d

Requirements
Must have
• Employee Info:
• Melissa Thornbury
• Chief Executive Offer
• m: 919.537.2846
• w: 919.362.4178
• f: 919.685.3907
• mthornbury@brightlinetattooremoval.example
• Address:
• 4615 Oakmere Pkwy, Suite 210
• Raleigh, NC 27654
• Website:
• www.brightlinetattooremoval.example
Nice to have
• Myabe business name on back or logo on back and employee info on the front

```html
<!DOCTYPE html>
<html lang="en">
<head>
<meta charset="utf-8">
<title>Brightline Tattoo Removal — Business Cards</title>
<link href="https://fonts.googleapis.com/css2?family=Arimo:wght@400;700&display=swap" rel="stylesheet">
<style>
  :root {
    --card-black: #121212;
    --stage: #5c5c5c;
    --ink-white: #ffffff;
    --ink-soft: #f5f5f5;
    --ink-grey: #a9a9a9;
    --rule-grey: #9d9d9d;
  }
  * { margin: 0; padding: 0; box-sizing: border-box; }
  html, body { width: 1200px; height: 782px; overflow: hidden; }
  body {
    background: var(--stage);
    font-family: "Arimo", Arial, sans-serif;
    color: var(--ink-white);
    position: relative;
  }
  .card {
    position: absolute;
    top: 242px;
    width: 520px;
    height: 297px;
    background: var(--card-black);
    box-shadow: 0 6px 18px rgba(0,0,0,0.35);
  }
  .card--back { left: 620px; }
  .card--front { left: 60px; }

  .wordmark {
    text-align: center;
    font-weight: 400;
    color: var(--ink-white);
  }
  .wordmark__name {
    display: block;
    font-size: 40px;
    letter-spacing: 3px;
    line-height: 1;
  }
  .wordmark__service {
    display: flex;
    align-items: center;
    justify-content: center;
    gap: 10px;
    margin-top: 14px;
    font-size: 15px;
    letter-spacing: 4px;
  }
  .wordmark__service::before,
  .wordmark__service::after {
    content: "";
    width: 22px;
    height: 1px;
    background: var(--rule-grey);
  }

  .card--back .wordmark {
    position: absolute;
    left: 0; right: 0; top: 92px;
  }
  .card--back .website {
    position: absolute;
    left: 0; right: 0; top: 200px;
    text-align: center;
    font-size: 15px;
    color: var(--ink-soft);
  }

  .card--front .wordmark {
    position: absolute;
    right: 20px; top: 152px;
    width: 200px;
  }
  .card--front .wordmark__name { font-size: 28px; letter-spacing: 2px; }
  .card--front .wordmark__service {
    font-size: 11px; letter-spacing: 2.5px; margin-top: 12px; gap: 8px;
  }
  .card--front .wordmark__service::before,
  .card--front .wordmark__service::after { width: 16px; }

  .person {
    position: absolute;
    left: 26px; top: 28px;
  }
  .person__name {
    font-weight: 700;
    font-size: 17px;
    letter-spacing: 0.5px;
    text-transform: uppercase;
  }
  .person__title {
    font-size: 12px;
    color: var(--ink-grey);
    margin-top: 3px;
  }
  .address {
    position: absolute;
    left: 26px; top: 100px;
    font-style: normal;
    font-size: 12px;
    line-height: 1.35;
    color: var(--ink-soft);
  }
  .contacts {
    position: absolute;
    left: 26px; top: 150px;
    list-style: none;
    font-size: 12px;
    line-height: 1.45;
    color: var(--ink-soft);
  }
  .contacts li { display: flex; align-items: center; gap: 5px; }
  .contacts svg { width: 10px; height: 10px; fill: var(--ink-soft); flex: none; }
</style>
</head>
<body>

  <section class="card card--back" aria-label="Card back">
    <div class="wordmark">
      <span class="wordmark__name">BRIGHTLINE</span>
      <span class="wordmark__service">TATTOO REMOVAL</span>
    </div>
    <p class="website">www.brightlinetattooremoval.example</p>
  </section>

  <section class="card card--front" aria-label="Card front">
    <div class="person">
      <p class="person__name">Melissa Thornbury</p>
      <p class="person__title">Chief Executive Officer</p>
    </div>
    <address class="address">
      4615 Oakmere Pkwy, Suite 210<br>
      Raleigh, NC 27654
    </address>
    <ul class="contacts">
      <li>
        <svg viewBox="0 0 12 12" aria-label="Mobile"><path d="M3 0h6a1 1 0 0 1 1 1v10a1 1 0 0 1-1 1H3a1 1 0 0 1-1-1V1a1 1 0 0 1 1-1zm0 1.5v8h6v-8z"/></svg>
        919.537.2846
      </li>
      <li>
        <svg viewBox="0 0 12 12" aria-label="Phone"><path d="M2.5 0.5l2 2.5-1.2 1.3a7 7 0 0 0 4.4 4.4L9 7.5l2.5 2-1.5 2C5 11.5 0.5 7 0.5 2z"/></svg>
        919.362.4178
      </li>
      <li>
        <svg viewBox="0 0 12 12" aria-label="Fax"><path d="M3 0h5l1 1v3H3zM1 5h10a1 1 0 0 1 1 1v5H0V6a1 1 0 0 1 1-1zm2 3v2h6V8z"/></svg>
        919.685.3907
      </li>
      <li>
        <svg viewBox="0 0 12 12" aria-label="Email"><path d="M0 2h12v8H0zm1 1v.3l5 3.4 5-3.4V3z"/></svg>
        mthornbury@brightlinetattooremoval.example
      </li>
    </ul>
    <div class="wordmark">
      <span class="wordmark__name">BRIGHTLINE</span>
      <span class="wordmark__service">TATTOO REMOVAL</span>
    </div>
  </section>

</body>
</html>
```